RV7 - Rapid Vigil Field Operations Suite

I need an introductory website for RV7 which describes the features of the product and the ease of use of the product. The product is focused on Preparing for an incident using Volunteer and Resource management and then responding to an incident with Incident Management, Team Management, Task Management and Communication Management. Once a situation is handled, the application provides complete reporting on each of the above aspects

Target Market(s)

Local Government entities, specifically the emergency department directors or coordinators

Industry/Entity Type

Government Office

Coding

Coded - Design and coding required

Font styles to use
Sans Serif

Requirements
Must have
• Clear layout with modern images. I want to be able to get a clear understanding of the features of the product and the ease of use. I would like to high light how the application helps in Communication Management, Team Management, Task Management and Incident Managements. Also, how the use of application helps to get an immediate snap shot of how well an incident was handled. I want to highlight how the Dashboard provides a quick look at the Incident(s) being managed
Nice to have
• I would like to in the future add videos to the site. At this point don't have any ideas about nice to have features
Should not have
• traditional designs. I am looking for a slick, modern looking website. Clean design is the key.

```html
<!DOCTYPE html>
<html lang="en">
<head>
<meta charset="utf-8">
<title>RV7 - Rapid Vigil Field Operations Suite</title>
<link href="https://fonts.googleapis.com/css2?family=Raleway:wght@300;400;500;600&family=Open+Sans:ital,wght@0,400;0,600;1,400&display=swap" rel="stylesheet">
<style>
  :root {
    --brand-blue: #1e5aa8;
    --navy: #1d4fa0;
    --hero-blue: #2b6cc2;
    --leaf: #6a9a2a;
    --lime: #8cc63f;
    --ink: #3c3c3c;
    --muted: #9a9a9a;
    --panel: #efefef;
    --footer: #0b1626;
    --white: #ffffff;
  }
  * { box-sizing: border-box; margin: 0; padding: 0; }
  html, body { width: 1200px; height: 2166px; overflow: hidden; }
  body { position: relative; background: var(--white); font-family: "Open Sans", Arial, sans-serif; color: var(--ink); }
  .abs { position: absolute; }

  /* header */
  .site-header { position: absolute; left: 0; top: 0; width: 1200px; height: 84px; background: var(--white); }
  .brand { position: absolute; left: 169px; top: 22px; display: flex; align-items: center; gap: 12px; }
  .brand-dot { width: 48px; height: 48px; border-radius: 50%; background: var(--brand-blue); }
  .brand-name { font-family: "Raleway", Arial, sans-serif; font-weight: 500; font-size: 34px; color: var(--brand-blue); }
  .main-nav a { position: absolute; top: 45px; font-family: "Raleway", Arial, sans-serif; font-size: 14.5px; color: #444; text-decoration: none; }
  .main-nav a.is-active { color: var(--leaf); }

  /* hero */
  .hero { position: absolute; left: 0; top: 84px; width: 1200px; height: 444px; background: linear-gradient(100deg, #3a72b8 0%, #2c68bd 45%, #4a86d2 75%, #2f65b4 100%); }
  .hero-visual { position: absolute; left: 620px; top: 0; width: 420px; height: 444px; background: linear-gradient(180deg, rgba(255,255,255,0.18), rgba(20,50,110,0.25)); }
  .hero-title { position: absolute; left: 182px; top: 145px; font-family: "Raleway", Arial, sans-serif; font-weight: 500; font-size: 29px; line-height: 36px; color: var(--white); }
  .hero-text { position: absolute; left: 183px; top: 226px; width: 350px; font-size: 12px; line-height: 18px; color: #dce8f8; }
  .btn-ghost { position: absolute; left: 183px; top: 281px; width: 104px; height: 32px; border: 1.5px solid var(--white); color: var(--white); font-size: 13px; line-height: 29px; text-align: center; }
  .hero-arrow { position: absolute; top: 190px; }

  /* features */
  .feature { position: absolute; top: 546px; width: 220px; text-align: center; }
  .feature svg { display: block; margin: 0 auto; }
  .feature h3 { margin-top: 14px; font-family: "Raleway", Arial, sans-serif; font-weight: 500; font-size: 19px; color: #333; }
  .feature p { margin-top: 8px; font-size: 11px; line-height: 17px; color: var(--muted); }

  /* why */
  .why { position: absolute; left: 0; top: 785px; width: 1200px; height: 388px; }
  .why h2 { position: absolute; left: 196px; top: 66px; font-family: "Raleway", Arial, sans-serif; font-weight: 400; font-size: 27px; color: var(--white); }
  .why-list { position: absolute; left: 200px; top: 113px; width: 430px; list-style: none; }
  .why-list li { position: relative; padding-left: 25px; margin-bottom: 11px; font-size: 12.5px; line-height: 18px; color: var(--white); }
  .why-list svg { position: absolute; left: 0; top: 3px; }
  .btn-lime { position: absolute; left: 201px; top: 300px; width: 115px; height: 34px; background: var(--lime); border: 2px solid var(--white); color: var(--white); font-size: 12.5px; line-height: 30px; text-align: center; }
  .why-devices { position: absolute; left: 686px; top: 35px; width: 311px; height: 353px; background: linear-gradient(180deg, #e9edf3, #b8c4d8); border-radius: 26px 26px 0 0; }

  /* reports */
  .reports { position: absolute; left: 0; top: 1173px; width: 1200px; height: 374px; background: linear-gradient(180deg, #f4f6f9 0%, #e9edf2 100%); }
  .reports-laptop { position: absolute; left: 118px; top: 62px; width: 489px; height: 245px; border-radius: 12px 12px 4px 4px; background: linear-gradient(180deg, #2c2f36, #50555f); }
  .reports h2 { position: absolute; left: 641px; top: 69px; font-family: "Raleway", Arial, sans-serif; font-weight: 400; font-size: 29px; color: #444; }
  .reports-text { position: absolute; left: 644px; top: 113px; width: 370px; font-size: 12.5px; line-height: 17px; color: #555; }
  .reports-list { position: absolute; left: 654px; top: 170px; list-style: none; }
  .reports-list li { position: relative; padding-left: 12px; height: 28.5px; font-size: 12.5px; color: #444; }
  .reports-list li::before { content: ""; position: absolute; left: 0; top: 4px; border-left: 6px solid var(--navy); border-top: 5px solid transparent; border-bottom: 5px solid transparent; }
  .btn-navy { position: absolute; left: 644px; top: 274px; width: 103px; height: 29px; background: var(--navy); color: var(--white); font-size: 11.5px; line-height: 29px; text-align: center; border-radius: 2px; }

  /* testimonials */
  .testimonials { position: absolute; left: 0; top: 1547px; width: 1200px; height: 316px; background: var(--panel); overflow: hidden; }
  .testimonials h2 { position: absolute; left: 0; width: 1200px; top: 40px; text-align: center; font-family: "Raleway", Arial, sans-serif; font-weight: 400; font-size: 25px; color: #333; }
  .quote-card { position: absolute; top: 98px; height: 159px; background: var(--white); border: 1px solid #dedede; border-radius: 3px; overflow: hidden; }
  .quote-card.is-main { left: 406px; width: 388px; }
  .quote-card.is-left { left: 153px; width: 198px; opacity: 0.55; }
  .quote-card.is-right { left: 862px; width: 178px; opacity: 0.55; }
  .avatar { position: absolute; top: 24px; width: 64px; height: 64px; border-radius: 50%; background: linear-gradient(160deg, #b58c6a, #6b5040); }
  .quote-text { position: absolute; top: 22px; width: 265px; font-size: 11px; line-height: 21px; font-style: italic; color: #555; }
  .quote-name { position: absolute; top: 118px; font-size: 12.5px; color: #222; white-space: nowrap; }
  .quote-name span { color: #3a7bd5; font-size: 11px; }
  .quote-arrow { position: absolute; top: 166px; }

  /* footer */
  .site-footer { position: absolute; left: 0; top: 1863px; width: 1200px; height: 303px; background: var(--footer); border-top: 3px solid var(--navy); }
  .footer-badge { position: absolute; left: 568px; top: -32px; width: 64px; height: 64px; border-radius: 50%; background: var(--white); font-family: "Raleway", Arial, sans-serif; font-weight: 600; font-size: 17px; color: var(--brand-blue); text-align: center; line-height: 64px; }
  .footer-col { position: absolute; top: 60px; }
  .footer-col h4 { font-family: "Raleway", Arial, sans-serif; font-weight: 400; font-size: 16.5px; color: #e4e8ee; margin-bottom: 10px; }
  .footer-col a { display: block; font-size: 11.5px; line-height: 24.5px; color: #a8b0bc; text-decoration: none; }
  .social { display: flex; gap: 3px; margin-top: 2px; }
  .social span { width: 24px; height: 24px; border: 1.5px solid #d8dce2; border-radius: 50%; }
  .footer-rule { position: absolute; left: 183px; top: 242px; width: 832px; height: 1px; background: #243246; }
  .copyright { position: absolute; left: 0; top: 259px; width: 1200px; text-align: center; font-size: 10.5px; color: #5f6a7a; }
</style>
</head>
<body>

<header class="site-header">
  <div class="brand"><span class="brand-dot"></span><span class="brand-name">RV7</span></div>
  <nav class="main-nav">
    <a href="#" class="is-active" style="left:484px">HOME</a>
    <a href="#" style="left:559px">ABOUT US</a>
    <a href="#" style="left:664px">TEAM</a>
    <a href="#" style="left:738px">SERVICES</a>
    <a href="#" style="left:839px">SUPPORT</a>
    <a href="#" style="left:939px">CONTACT</a>
  </nav>
</header>

<section class="hero" role="img" aria-label="Flooded neighbourhood street in blue tone with a presenter holding a phone that shows the incident map">
  <div class="hero-visual" role="img" aria-label="Presenter pointing at a smartphone showing an incident map"></div>
  <h1 class="hero-title">EMERGENCY - COMMAND,<br>CONTROL &amp; CO-ORDINATION</h1>
  <p class="hero-text">Mauris vel lacus vitae felis vestibulum volutpat imperdiet ac nisl Cum sociis natoque penatibus et maa</p>
  <a class="btn-ghost">Learn More</a>
  <svg class="hero-arrow" style="left:104px" width="20" height="36" viewBox="0 0 20 36"><path d="M16 4 L4 18 L16 32" fill="none" stroke="#fff" stroke-width="3"/></svg>
  <svg class="hero-arrow" style="left:1090px" width="20" height="36" viewBox="0 0 20 36"><path d="M4 4 L16 18 L4 32" fill="none" stroke="#fff" stroke-width="3"/></svg>
</section>

<section class="features">
  <div class="feature" style="left:215px">
    <svg width="124" height="124" viewBox="0 0 124 124"><circle cx="62" cy="62" r="58" fill="#fff" stroke="#c9dfa9" stroke-width="3"/><circle cx="62" cy="62" r="50" fill="none" stroke="#7fb03b" stroke-width="3"/>
      <g fill="var(--navy)"><circle cx="62" cy="50" r="8"/><circle cx="47" cy="55" r="6"/><circle cx="77" cy="55" r="6"/><path d="M48 80 Q48 62 62 62 Q76 62 76 80Z"/><path d="M36 78 Q36 64 47 64 Q52 64 54 67 Q47 70 46 78Z"/><path d="M88 78 Q88 64 77 64 Q72 64 70 67 Q77 70 78 78Z"/></g></svg>
    <h3>Team Management</h3>
    <p>Mauris vel lacus vitae felis vestibulum<br>volutpat eu imperdiet ac nisl</p>
  </div>
  <div class="feature" style="left:491px">
    <svg width="124" height="124" viewBox="0 0 124 124"><circle cx="62" cy="62" r="58" fill="#fff" stroke="#c9dfa9" stroke-width="3"/><circle cx="62" cy="62" r="50" fill="none" stroke="#7fb03b" stroke-width="3"/>
      <path d="M62 40 A22 22 0 1 0 84 62" fill="none" stroke="var(--navy)" stroke-width="5"/><path d="M62 62 L72 50" stroke="var(--navy)" stroke-width="4"/><circle cx="62" cy="62" r="4" fill="var(--navy)"/><path d="M52 74 l-6 6 l8 2z" fill="#7fb03b"/></svg>
    <h3>Incident Management</h3>
    <p>Mauris vel lacus vitae felis vestibulum<br>volutpat eu imperdiet ac nisl</p>
  </div>
  <div class="feature" style="left:782px">
    <svg width="124" height="124" viewBox="0 0 124 124"><circle cx="62" cy="62" r="58" fill="#fff" stroke="#c9dfa9" stroke-width="3"/><circle cx="62" cy="62" r="50" fill="none" stroke="#7fb03b" stroke-width="3"/>
      <path d="M48 38 H76 M48 86 H76 M51 38 Q51 56 62 62 Q73 56 73 38 M51 86 Q51 68 62 62 Q73 68 73 86" fill="none" stroke="var(--navy)" stroke-width="4"/><path d="M55 84 Q58 72 62 70 Q66 72 69 84Z" fill="#7fb03b"/></svg>
    <h3>Task Management</h3>
    <p>Mauris vel lacus vitae felis vestibulum<br>volutpat eu imperdiet ac nisl</p>
  </div>
</section>

<section class="why">
  <svg class="abs" style="left:0;top:0" width="1200" height="388" viewBox="0 0 1200 388">
    <defs><linearGradient id="whyBand" x1="0" y1="0" x2="1" y2="0.3"><stop offset="0" stop-color="#5d9a2c"/><stop offset="0.45" stop-color="#2f7a6a"/><stop offset="1" stop-color="#1a4fa3"/></linearGradient></defs>
    <path d="M0 38 Q720 -30 1200 48 L1200 388 L0 388Z" fill="url(#whyBand)"/>
  </svg>
  <h2>Why adopt RV7</h2>
  <ul class="why-list">
    <li><svg width="16" height="12" viewBox="0 0 16 12"><path d="M1 6 L6 11 L15 1" fill="none" stroke="#fff" stroke-width="2.5"/></svg>Easy system to register volunteers</li>
    <li><svg width="16" height="12" viewBox="0 0 16 12"><path d="M1 6 L6 11 L15 1" fill="none" stroke="#fff" stroke-width="2.5"/></svg>Accurate identification of number of CERT Volunteers available to help in an incident</li>
    <li><svg width="16" height="12" viewBox="0 0 16 12"><path d="M1 6 L6 11 L15 1" fill="none" stroke="#fff" stroke-width="2.5"/></svg>Efficient Communication mechanism to reach out to the volunteers via SMS</li>
    <li><svg width="16" height="12" viewBox="0 0 16 12"><path d="M1 6 L6 11 L15 1" fill="none" stroke="#fff" stroke-width="2.5"/></svg>Rich graphical visualization of Incidents &amp; Damages associated with the incidents</li>
  </ul>
  <a class="btn-lime">READ MORE</a>
  <div class="why-devices" role="img" aria-label="Two smartphones showing the volunteer menu and notifications screens"></div>
</section>

<section class="reports">
  <div class="reports-laptop" role="img" aria-label="Laptop showing the reports dashboard with charts and a world map"></div>
  <h2>Reports Console</h2>
  <p class="reports-text">City Officials and Emergency Management Officials can get access to instant statistics on</p>
  <ul class="reports-list">
    <li>Incident Management</li>
    <li>Volunteer Management</li>
    <li>Damage Assessment</li>
  </ul>
  <a class="btn-navy">READ MORE</a>
</section>

<section class="testimonials">
  <h2>Testimonials</h2>
  <div class="quote-card is-left">
    <p class="quote-text" style="left:-110px">Mauris vel lacus vitae felis vestibulum volutpat E eu imperdiet ac nisl Cum sociis natoque penatibus et magnis dis parturient montes nascetur ridiculus mus In iaculis facilisis massa Etiam eu urna Sed porta</p>
    <p class="quote-name" style="left:-70px">Dana Morrow, <span>Company Name</span></p>
  </div>
  <div class="quote-card is-main">
    <div class="avatar" style="left:18px" role="img" aria-label="Reviewer portrait"></div>
    <p class="quote-text" style="left:97px">Mauris vel lacus vitae felis vestibulum volutpat E eu imperdiet ac nisl Cum sociis natoque penatibus et magnis dis parturient montes nascetur ridiculus mus In iaculis facilisis massa Etiam eu urna Sed porta</p>
    <p class="quote-name" style="left:97px">Dana Morrow, <span>Company Name</span></p>
  </div>
  <div class="quote-card is-right">
    <div class="avatar" style="left:18px" role="img" aria-label="Reviewer portrait"></div>
    <p class="quote-text" style="left:97px">Mauris vel lacus vitae felis vestibulum volutpat E eu imperdiet ac nisl Cum sociis natoque penatibus et magnis dis parturient montes nascetur ridiculus mus In iaculis facilisis massa Etiam eu urna Sed porta</p>
    <p class="quote-name" style="left:97px">Dana Morrow, <span>Company Name</span></p>
  </div>
  <svg class="quote-arrow" style="left:362px" width="14" height="26" viewBox="0 0 14 26"><path d="M12 2 L2 13 L12 24" fill="none" stroke="#9a9a9a" stroke-width="2"/></svg>
  <svg class="quote-arrow" style="left:824px" width="14" height="26" viewBox="0 0 14 26"><path d="M2 2 L12 13 L2 24" fill="none" stroke="#9a9a9a" stroke-width="2"/></svg>
</section>

<footer class="site-footer">
  <div class="footer-badge">RV7</div>
  <div class="footer-col" style="left:192px"><h4>COMPANY</h4><a>Home</a><a>About Us</a><a>Support</a><a>Solution</a></div>
  <div class="footer-col" style="left:349px"><h4>OUR SERVCIES</h4><a>Duis quam Nam</a><a>Eget lacus</a><a>Aliquam erat</a><a>Volutpat Quisque</a></div>
  <div class="footer-col" style="left:539px"><h4>LINKS</h4><a>Price</a><a>Quote</a><a>Free Trail</a></div>
  <div class="footer-col" style="left:684px"><h4>RESOURCES</h4><a>Support</a><a>Blogs</a><a>Contact Us</a></div>
  <div class="footer-col" style="left:861px"><h4>FOLLOW US</h4><div class="social"><span></span><span></span><span></span><span></span></div></div>
  <div class="footer-rule"></div>
  <p class="copyright">© 2016 Company Name  All right reserved  Term of Use</p>
</footer>

</body>
</html>
```